Veldmark Supplies Business Card

Professional business card that stand out to our potential customers. Front and back with clean modern design

Industry/Entity Type

Oil and gas

Contact Information for Business Card

Name, address, website , office phone and cell number

Requirements
Must have
• Editable files for each employee

```html
<!DOCTYPE html>
<html lang="en">
<head>
<meta charset="utf-8">
<title>Veldmark Supplies Business Card</title>
<link href="https://fonts.googleapis.com/css2?family=Arimo:wght@400;700&display=swap" rel="stylesheet">
<style>
  :root {
    --bg: #3a3a3a;
    --red: #ff0000;
    --white: #ffffff;
    --cyan: #1fa8d0;
    --card-shadow: rgba(0,0,0,0.45);
  }
  html, body {
    margin: 0;
    padding: 0;
    overflow: hidden;
  }
  body {
    width: 1200px;
    height: 689px;
    background: var(--bg);
    font-family: "Arimo", Arial, sans-serif;
    position: relative;
  }
  .card {
    position: absolute;
    top: 196px;
    width: 520px;
    height: 297px;
    border-radius: 18px;
    overflow: hidden;
    box-shadow: 0 12px 30px var(--card-shadow);
  }
  .card--front {
    left: 50px;
    background: var(--red);
    display: flex;
    align-items: center;
    justify-content: center;
  }
  .card--back {
    left: 630px;
    background: var(--white);
    display: flex;
  }
  .brand {
    display: flex;
    align-items: center;
    gap: 12px;
  }
  .brand__mark {
    width: 22px;
    height: 22px;
  }
  .brand__name {
    font-weight: 700;
    font-size: 26px;
    letter-spacing: 1px;
    text-transform: uppercase;
  }
  .card--front .brand__mark { background: var(--white); }
  .card--front .brand__name { color: var(--white); }
  .back__brand-panel {
    width: 232px;
    display: flex;
    align-items: center;
    justify-content: center;
  }
  .back__brand-panel .brand { flex-direction: column; gap: 10px; }
  .back__brand-panel .brand__mark { background: var(--red); width: 18px; height: 18px; }
  .back__brand-panel .brand__name { color: var(--red); font-size: 18px; text-align: center; line-height: 1.2; }
  .back__divider {
    width: 5px;
    background: var(--cyan);
  }
  .back__contact {
    flex: 1;
    background: var(--red);
    color: var(--white);
    padding: 58px 0 0 30px;
  }
  .contact__name {
    color: var(--cyan);
    font-weight: 700;
    font-size: 24px;
    margin: 0;
  }
  .contact__title {
    font-size: 13px;
    margin: 2px 0 16px;
  }
  .contact__address {
    font-size: 13px;
    line-height: 1.35;
    font-style: normal;
    margin-bottom: 12px;
  }
  .contact__list {
    list-style: none;
    margin: 0;
    padding: 0;
    font-size: 13px;
    line-height: 1.5;
  }
  .contact__list li {
    display: flex;
    align-items: center;
    gap: 8px;
  }
  .contact__icon {
    width: 11px;
    height: 11px;
    flex: none;
  }
</style>
</head>
<body>
  <section class="card card--front" aria-label="Card front">
    <div class="brand">
      <span class="brand__mark"></span>
      <span class="brand__name">Veldmark Supplies</span>
    </div>
  </section>

  <section class="card card--back" aria-label="Card back">
    <div class="back__brand-panel">
      <div class="brand">
        <span class="brand__mark"></span>
        <span class="brand__name">Veldmark<br>Supplies</span>
      </div>
    </div>
    <div class="back__divider"></div>
    <div class="back__contact">
      <h1 class="contact__name">Dana Ortell</h1>
      <p class="contact__title">President</p>
      <address class="contact__address">4120 Harlow Crescent<br>Bramfield, Canada 58213</address>
      <ul class="contact__list">
        <li>
          <svg class="contact__icon" viewBox="0 0 12 12"><path d="M2.5 1 L4.5 1 L5 3.5 L3.8 4.4 Q5 7 7.6 8.2 L8.5 7 L11 7.5 L11 9.5 Q10.5 11 9 11 Q1 10 1 3 Q1 1.5 2.5 1Z" fill="var(--cyan)"/></svg>
          555-214-0387
        </li>
        <li>
          <svg class="contact__icon" viewBox="0 0 12 12"><rect x="3" y="0.5" width="6" height="11" rx="1" fill="none" stroke="var(--cyan)" stroke-width="1.3"/><circle cx="6" cy="9.5" r="0.7" fill="var(--cyan)"/></svg>
          555-381-7720
        </li>
        <li>
          <svg class="contact__icon" viewBox="0 0 12 12"><rect x="0.5" y="2" width="11" height="8" fill="var(--cyan)"/><path d="M0.5 2 L6 6.5 L11.5 2" fill="none" stroke="var(--red)" stroke-width="1"/></svg>
          info@veldmarksupplies.com
        </li>
        <li>
          <svg class="contact__icon" viewBox="0 0 12 12"><circle cx="6" cy="6" r="5" fill="none" stroke="var(--cyan)" stroke-width="1.3"/><ellipse cx="6" cy="6" rx="2" ry="5" fill="none" stroke="var(--cyan)" stroke-width="1"/><line x1="1" y1="6" x2="11" y2="6" stroke="var(--cyan)" stroke-width="1"/></svg>
          www.veldmarksupplies.com
        </li>
      </ul>
    </div>
  </section>
</body>
</html>
```